Covid 19 Exit Strategy one page brochure

I would like to design, and will need URGENT help, a brochure detailing a Covid 19 Exit Strategy plan. This brochure will need to be understood easily and the graphics inside should make it easy for people to understand without reading the entire text. This project is quite urgent and needs to be completed THIS WEEK - by Saturday may 16th at the latest. I am attaching two examples. I will provide the text.

```html
<!DOCTYPE html>
<html lang="en">
<head>
<meta charset="utf-8">
<title>Coronavirus COVID-19 – The Exit Strategy</title>
<link href="https://fonts.googleapis.com/css2?family=Montserrat:wght@300;400;500;600;700;800&display=swap" rel="stylesheet">
<style>
  :root{
    --navy:#123f5c;
    --band-orange:#dc8f3a;
    --yellow:#fcc72c;
    --gold-dark:#c9a024;
    --pink:#e91e50;
    --purple:#5e60a8;
    --purple-dark:#4b4d92;
    --cyan:#5ac4d0;
    --orange:#f5a82b;
    --white:#ffffff;
  }
  *{margin:0;padding:0;box-sizing:border-box}
  html,body{width:925px;height:1200px;overflow:hidden;background:var(--white)}
  body{font-family:"Montserrat",sans-serif;color:var(--white)}
  .brochure{position:relative;width:925px;height:1200px;overflow:hidden}
  .backdrop,.arrows{position:absolute;left:0;top:0;width:925px;height:1200px}
  .abs{position:absolute}

  .masthead{left:0;width:925px;text-align:center}
  .masthead__title{top:55px;font-size:37px;font-weight:700;letter-spacing:.5px}
  .masthead__sub{top:110px;font-size:29px;font-weight:500}

  .title{left:73px;color:var(--navy);font-weight:800;line-height:1}
  .title__the{top:193px;font-size:30px}
  .title__exit{top:222px;font-size:131px;letter-spacing:-3px}
  .title__strategy{top:336px;font-size:55px;letter-spacing:-1px}
  .title__question{left:75px;top:398px;font-size:13px;font-weight:700;color:var(--navy)}
  .objective{left:71px;top:426px;width:310px;height:74px;background:var(--navy);padding:11px 14px}
  .objective h3{font-size:13px;font-weight:700;margin-bottom:3px}
  .objective p{font-size:11px;font-weight:400;line-height:1.45}

  .step-title{font-weight:700;font-size:19px}
  .step-body{font-weight:300;font-size:15.5px;line-height:23.5px;text-align:justify}

  .ensure__title{left:513px;top:326px;font-size:38px;font-weight:700}
  .ensure__body{left:513px;top:378px;font-size:15.5px;font-weight:300}

  .foresee{left:99px;top:662px;width:400px;font-size:16.5px;font-weight:300;line-height:25.5px}
  .foresee strong{font-weight:700}

  .testing__title{left:46px;top:855px}
  .testing__body{left:46px;top:888px;width:402px}

  .monitoring__title{left:554px;top:840px}
  .monitoring__body{left:554px;top:873px;width:328px}

  .barrier__title{left:142px;top:1032px}
  .barrier__body{left:142px;top:1063px;width:369px}

  .protect{left:673px;top:1041px;font-size:16px;font-weight:300;line-height:24px}
  .protect strong{font-weight:700}

  .footer__brand{left:545px;top:1138px;font-size:42px;font-weight:700}
  .footer__contacts{left:733px;top:1137px;font-size:10.5px;font-weight:400;line-height:16.5px;list-style:none}
  .footer__contacts li::before{content:"";display:inline-block;width:7px;height:7px;border:1.2px solid var(--white);border-radius:50%;margin-right:3px;vertical-align:-1px}

  .presenter{left:757px;top:433px;width:143px;height:406px;border-radius:40px 40px 10px 10px;
    background:linear-gradient(180deg,#3b2c2a 0%,#1e1e22 35%,#141417 100%);opacity:.9}
  .icon{position:absolute}
</style>
</head>
<body>
<main class="brochure">
  <svg class="backdrop" viewBox="0 0 925 1200" aria-hidden="true">
    <rect width="925" height="1200" fill="var(--navy)"/>
    <polygon points="0,165 925,132 925,210 0,172" fill="var(--band-orange)"/>
    <polygon points="0,172 462,191 462,523 0,523" fill="var(--yellow)"/>
    <polygon points="462,191 925,210 925,507 514,628 514,700 462,700" fill="var(--pink)"/>
    <polygon points="514,628 925,507 925,960 524,1001 524,840 514,840" fill="var(--orange)"/>
    <polygon points="0,523 570,523 570,611 514,628 514,840 524,840 0,729" fill="var(--purple)"/>
    <polygon points="0,523 85,523 0,594" fill="var(--gold-dark)"/>
    <polygon points="85,523 85,631 0,631 0,594" fill="var(--purple-dark)"/>
    <polygon points="0,729 524,840 524,950 0,1016" fill="var(--cyan)"/>
    <polygon points="0,1016 524,950 524,1200 0,1200" fill="var(--pink)"/>
    <polygon points="524,1001 925,960 925,1126 524,1126" fill="var(--purple)"/>
    <rect x="526" y="1126" width="399" height="74" fill="var(--navy)"/>
  </svg>

  <svg class="arrows" viewBox="0 0 925 1200" aria-hidden="true" fill="none" stroke="var(--white)" stroke-linecap="round">
    <path d="M383 258 C410 225 450 225 492 250" stroke-width="9"/>
    <polygon points="480,230 510,256 476,268" fill="var(--white)" stroke="none"/>
    <path d="M578 445 C590 490 560 530 498 548" stroke-width="10"/>
    <polygon points="505,530 474,560 514,565" fill="var(--white)" stroke="none"/>
    <path d="M500 690 C530 660 565 660 592 672" stroke-width="8"/>
    <polygon points="582,655 610,680 576,690" fill="var(--white)" stroke="none"/>
    <path d="M540 890 C530 915 505 918 478 915" stroke-width="8"/>
    <polygon points="484,900 460,918 486,932" fill="var(--white)" stroke="none"/>
    <path d="M198 950 C215 948 228 958 233 975" stroke-width="3"/>
    <polygon points="224,972 242,996 244,968" fill="var(--white)" stroke="none"/>
    <path d="M486 1036 C502 1022 520 1022 536 1032" stroke-width="4"/>
    <polygon points="530,1022 550,1040 526,1044" fill="var(--white)" stroke="none"/>
  </svg>

  <h1 class="abs masthead masthead__title">CORONAVIRUS COVID-19</h1>
  <h2 class="abs masthead masthead__sub">INFORMATION AND GUIDELINES</h2>

  <div class="abs title title__the">THE</div>
  <div class="abs title title__exit">EXIT</div>
  <div class="abs title title__strategy">STRATEGY</div>
  <div class="abs title__question">WHAT DOES THE STRATEGY CONSIST OF?</div>
  <div class="abs objective">
    <h3>OBJECTIVE</h3>
    <p>To gradually phase out the restrictions imposed<br>to curb the spread</p>
  </div>

  <svg class="icon" style="left:512px;top:224px" width="114" height="80" viewBox="0 0 114 80" aria-hidden="true" fill="var(--white)">
    <rect x="0" y="72" width="114" height="8"/>
    <rect x="6" y="24" width="102" height="50"/>
    <rect x="34" y="0" width="46" height="74" rx="6"/>
    <g fill="var(--pink)">
      <rect x="54" y="8" width="6" height="20"/><rect x="47" y="15" width="20" height="6"/>
      <rect x="50" y="52" width="14" height="22"/>
      <rect x="14" y="34" width="5" height="5"/><rect x="22" y="34" width="5" height="5"/>
      <rect x="14" y="44" width="5" height="5"/><rect x="22" y="44" width="5" height="5"/>
      <rect x="14" y="54" width="5" height="5"/><rect x="22" y="54" width="5" height="5"/>
      <rect x="87" y="34" width="5" height="5"/><rect x="95" y="34" width="5" height="5"/>
      <rect x="87" y="44" width="5" height="5"/><rect x="95" y="44" width="5" height="5"/>
      <rect x="87" y="54" width="5" height="5"/><rect x="95" y="54" width="5" height="5"/>
    </g>
  </svg>
  <div class="abs ensure__title">Ensure,</div>
  <div class="abs ensure__body">at all times, sufficient hospital capacities.</div>

  <div class="abs presenter" role="img" aria-label="Illustration of a man in a dark suit wearing a face mask, raising a fist"></div>

  <svg class="icon" style="left:97px;top:549px" width="110" height="92" viewBox="0 0 110 92" aria-hidden="true" fill="none" stroke="var(--white)" stroke-width="2.5">
    <circle cx="20" cy="14" r="12"/>
    <line x1="20" y1="8" x2="20" y2="15"/><circle cx="20" cy="20" r="1" fill="var(--white)"/>
    <polyline points="30,52 62,22 98,54"/>
    <polyline points="38,46 38,88 90,88 90,46"/>
    <rect x="56" y="58" width="16" height="30"/>
    <line x1="102" y1="60" x2="102" y2="88"/>
    <line x1="0" y1="68" x2="18" y2="68" stroke-width="5"/>
    <polygon points="16,60 26,68 16,76" fill="var(--white)" stroke="none"/>
  </svg>
  <p class="abs foresee">Foresee the possibility of reintroducing <strong>stricter measures</strong> in the event of a strong resurgence of the virus among the population</p>

  <svg class="icon" style="left:47px;top:771px" width="70" height="68" viewBox="0 0 70 68" aria-hidden="true" fill="none" stroke="var(--white)" stroke-width="2">
    <rect x="2" y="6" width="46" height="60"/>
    <rect x="16" y="2" width="18" height="8"/>
    <rect x="9" y="18" width="8" height="8"/><line x1="21" y1="22" x2="40" y2="22"/>
    <rect x="9" y="32" width="8" height="8"/><line x1="21" y1="36" x2="30" y2="36"/>
    <rect x="32" y="30" width="36" height="36"/>
    <line x1="40" y1="36" x2="40" y2="62"/><line x1="48" y1="36" x2="48" y2="62"/>
    <line x1="56" y1="36" x2="56" y2="62"/><line x1="63" y1="36" x2="63" y2="62"/>
  </svg>
  <div class="abs step-title testing__title">Foster testing capacities</div>
  <p class="abs step-body testing__body">and support research in particular with regard to tests to measure the acquired immunity ofthe population.</p>

  <svg class="icon" style="left:548px;top:725px" width="138" height="102" viewBox="0 0 138 102" aria-hidden="true" fill="none" stroke="var(--white)">
    <rect x="4" y="4" width="112" height="76" rx="4" stroke-width="7"/>
    <rect x="46" y="86" width="30" height="10" fill="var(--white)" stroke="none"/>
    <polyline points="20,45 36,45 42,32 50,58 56,40 64,45" stroke-width="3"/>
    <circle cx="86" cy="58" r="18" stroke-width="7" fill="var(--orange)"/>
    <line x1="100" y1="72" x2="128" y2="98" stroke-width="9" stroke-linecap="round"/>
  </svg>
  <div class="abs step-title monitoring__title">Provide close monitoring</div>
  <p class="abs step-body monitoring__body">Provide close monitoring of the evolution ofthe pandemic duringthe entire exit, as well as the secondary effects of the confinement.</p>

  <svg class="icon" style="left:46px;top:1043px" width="82" height="74" viewBox="0 0 82 74" aria-hidden="true" fill="var(--white)" stroke="var(--white)" stroke-width="1.5">
    <g id="person">
      <circle cx="6" cy="4" r="3.5" stroke="none"/>
      <rect x="2" y="9" width="8" height="12" rx="2" stroke="none"/>
      <rect x="3" y="20" width="2.5" height="8" stroke="none"/><rect x="6.5" y="20" width="2.5" height="8" stroke="none"/>
    </g>
    <use href="#person" x="35"/><use href="#person" x="70"/>
    <use href="#person" y="44"/><use href="#person" x="35" y="44"/><use href="#person" x="70" y="44"/>
    <line x1="15" y1="16" x2="28" y2="16"/><line x1="50" y1="16" x2="63" y2="16"/>
    <line x1="15" y1="60" x2="28" y2="60"/><line x1="50" y1="60" x2="63" y2="60"/>
    <line x1="6" y1="32" x2="6" y2="42" stroke-dasharray="2 2"/>
    <line x1="41" y1="32" x2="41" y2="42" stroke-dasharray="2 2"/>
    <line x1="76" y1="32" x2="76" y2="42" stroke-dasharray="2 2"/>
  </svg>
  <div class="abs step-title barrier__title">Apply basic barrier gestures</div>
  <p class="abs step-body barrier__body">and reinforce them with other specific measures, including in the workplace, to minimize the risk of an uncontrolled spread ofthe virus</p>

  <svg class="icon" style="left:601px;top:1033px" width="60" height="60" viewBox="0 0 60 60" aria-hidden="true" fill="none" stroke="var(--white)" stroke-width="2">
    <rect x="2" y="2" width="22" height="30" rx="2"/>
    <line x1="8" y1="10" x2="18" y2="10"/><line x1="8" y1="16" x2="18" y2="16"/>
    <path d="M13 32 V44 C13 52 22 54 30 52 H38"/>
    <rect x="36" y="46" width="20" height="12" rx="6"/>
    <path d="M44 26 L36 18 C32 14 36 8 40 11 L44 14 L48 11 C52 8 56 14 52 18 Z"/>
  </svg>
  <p class="abs protect"><strong>Protect</strong>, in particular,<br><strong>vulnerable</strong> groups.</p>

  <div class="abs footer__brand">LOGO</div>
  <ul class="abs footer__contacts">
    <li>+0 123 456 789</li>
    <li>info@yourmail.com</li>
    <li>www.yourcompany.com</li>
  </ul>
</main>
</body>
</html>
```